Food and Beverage Business Cards

We need business cards with logo designs for a consultant in the food and beverage industry. We specialize in helping restaurants fix operational and management problems.
Specific areas of expertise include:
-Steps of service
-Staff management tools
-Standard operating procedures
-Profit and loss management
-Inventory
-Point of sales
-Bar Menu
-Mystery shopper service
-Handling and managing suppliers

Target Market(s)

Restaurant and bar owners and managers

Industry/Entity Type

Business

Contact Information for Business Card

Mathieu Girardot
Q&T Consulting
phone: 15027390614
mathqt@sampleinbox.com

Font styles to use
Other font styles liked:
• Check out the screen shot font idea

Colors

Designer to choose colors to be used in the design.

Requirements
Must have
• Must include QR code (See attachment)
• Logo should reflect our specific focus on the drinks side of the industry.
• Areas of Expertise:
• -Service Steps
• -Staff management tools
• -S.O.P
• -P&L Management
• -Inventory
• -P.O.S
• -Bar Menu
• -Mystery Shopper Service
• -Handling and Managing Suppliers

```html
<!DOCTYPE html>
<html lang="en">
<head>
<meta charset="utf-8">
<title>Q&amp;T Consulting – Business Cards</title>
<link href="https://fonts.googleapis.com/css2?family=Open+Sans:wght@400;600;700&display=swap" rel="stylesheet">
<style>
  :root {
    --backdrop: #3b3431;
    --card: #1c1c1d;
    --ink-white: #f4f4f4;
    --ink-grey: #a9a9a9;
    --ink-soft: #8c8c8c;
    --rule: #9a9a9a;
    --badge-green: #2f5a36;
    --badge-grey: #cfcfcf;
    --badge-light: #e6e6e6;
  }
  * { box-sizing: border-box; margin: 0; padding: 0; }
  html, body {
    width: 1200px; height: 864px; overflow: hidden;
    background: var(--backdrop);
    font-family: "Open Sans", Arial, sans-serif;
  }
  .sheet {
    width: 1200px; height: 864px;
    display: flex; flex-direction: column; align-items: center; justify-content: center;
    gap: 28px;
  }
  .card {
    width: 700px; height: 400px;
    background: var(--card);
    border-radius: 4px;
    position: relative;
    box-shadow: 0 10px 28px rgba(0,0,0,.45);
  }

  /* Back: expertise */
  .card--back {
    display: flex; flex-direction: column; align-items: center;
    padding-top: 58px; text-align: center;
  }
  .wordmark {
    font-weight: 700; letter-spacing: 2px; line-height: 1;
  }
  .card--back .wordmark { font-size: 120px; color: var(--ink-grey); }
  .expertise-title {
    margin-top: 26px; font-size: 22px; font-weight: 700; color: var(--ink-grey);
  }
  .expertise-list {
    margin-top: 8px; font-size: 17px; line-height: 1.35; color: var(--ink-soft);
  }
  .badges {
    position: absolute; top: 46px; right: 48px; display: flex; gap: 10px;
  }
  .badge { width: 50px; height: 50px; border-radius: 50%; }
  .badge--green { background: var(--badge-green); }
  .badge--grey { background: var(--badge-grey); }
  .badge--light { background: var(--badge-light); }

  /* Front: contact */
  .card--front {
    display: flex; align-items: center;
  }
  .front-brand {
    width: 340px; display: flex; justify-content: center;
  }
  .card--front .wordmark { font-size: 104px; color: var(--ink-white); }
  .divider {
    width: 1px; height: 190px; background: var(--rule);
  }
  .contact {
    padding-left: 34px; color: var(--ink-white);
  }
  .contact-name {
    font-size: 22px; font-weight: 700; text-transform: uppercase; letter-spacing: .3px;
  }
  .contact-company {
    font-size: 17px; text-transform: uppercase; margin-bottom: 12px; letter-spacing: .5px;
  }
  .contact-line {
    display: flex; align-items: center; gap: 10px; font-size: 18px; line-height: 1.5;
  }
  .contact-line svg { width: 16px; height: 16px; fill: var(--ink-white); flex: none; }
</style>
</head>
<body>
<main class="sheet">
  <section class="card card--back" aria-label="Card back">
    <div class="badges">
      <span class="badge badge--green"></span>
      <span class="badge badge--grey"></span>
      <span class="badge badge--light"></span>
    </div>
    <div class="wordmark">Q&amp;T</div>
    <h2 class="expertise-title">Areas of Expertise</h2>
    <p class="expertise-list">
      Service Steps | Staff management tools | S.O.P | P&amp;L Management<br>
      Inventory | P.O.S | Bar Menu | Mystery Shopper Service<br>
      Handling and Managing Suppliers
    </p>
  </section>

  <section class="card card--front" aria-label="Card front">
    <div class="front-brand"><div class="wordmark">Q&amp;T</div></div>
    <div class="divider"></div>
    <div class="contact">
      <div class="contact-name">Mathieu Girardot</div>
      <div class="contact-company">Q&amp;T Consulting</div>
      <div class="contact-line">
        <svg viewBox="0 0 16 16" aria-hidden="true"><path d="M1 5c0-2 3-3 7-3s7 1 7 3v1h-4V5H5v1H1zM4 7h8l2 3v4H2v-4zm4 1.5a2 2 0 100 4 2 2 0 000-4z"/></svg>
        <span>15027390614</span>
      </div>
      <div class="contact-line">
        <svg viewBox="0 0 16 16" aria-hidden="true"><path d="M1 3h14v10H1zm1.5 1.2V5l5.5 4 5.5-4v-.8z"/></svg>
        <span>mathqt@sampleinbox.com</span>
      </div>
    </div>
  </section>
</main>
</body>
</html>
```